Brightbay Orthodontics business card design

Need a business card design that reflects our re-branding (orthodontic office - braces) and a new partnership with a pediatric dental office. We would like to include "for adults and children" on the card as well so adults know they are welcome to get their braces here as well. Office design is modern and would like business card to reflect a modern type look. Here's the text we would like to be included on the card:

Darren Wolcott, DDS, MSD
5214 West Linden Avenue, Suite 204
Cedarbrook, TX 76991
555-418-2637
www.brightbayortho.example
info@brightbayortho.example

Can we add the following to the existing designs? Darren Wolcott, DDS, MSD 5214 West Linden Avenue, Suite 204 Cedarbrook, TX 76991 555-418-2637

Does anyone have any more vertical designs available? Thanks!

Dental

```html
<!DOCTYPE html>
<html lang="en">
<head>
<meta charset="utf-8">
<title>Brightbay Orthodontics – Business Card</title>
<link href="https://fonts.googleapis.com/css2?family=Ubuntu:wght@400;500;700&display=swap" rel="stylesheet">
<style>
  :root {
    --blue: #1f66ad;
    --blue-light: #3a8fd0;
    --orange: #f39522;
    --grey-text: #8a8a8a;
    --ink: #2b2b2b;
    --card: #ffffff;
    --stage: #e6e8ea;
  }
  * { margin: 0; padding: 0; box-sizing: border-box; }
  html, body { width: 1200px; height: 1000px; overflow: hidden; }
  body {
    background: var(--stage);
    font-family: "Ubuntu", sans-serif;
    position: relative;
  }
  .card {
    position: absolute;
    width: 600px;
    height: 343px;
    background: var(--card);
    border-radius: 26px;
    overflow: hidden;
    box-shadow: 0 10px 28px rgba(0,0,0,0.22);
  }
  .card-front { left: 90px; top: 120px; }
  .card-back  { left: 510px; top: 537px; }

  .front-decoration {
    position: absolute; left: 350px; top: 0; width: 250px; height: 343px;
    background: linear-gradient(135deg, var(--blue) 0%, var(--blue-light) 55%, var(--blue) 100%);
  }
  .back-decoration {
    position: absolute; left: 400px; top: 255px; width: 200px; height: 88px;
    background: linear-gradient(90deg, var(--orange) 0%, var(--blue) 100%);
  }

  .holder-name {
    position: absolute; left: 46px; top: 104px;
    color: var(--blue); font-weight: 700; font-size: 31px;
  }
  .holder-degree {
    position: absolute; left: 64px; top: 146px;
    color: var(--grey-text); font-weight: 700; font-size: 18px;
  }
  .holder-email {
    position: absolute; left: 64px; top: 196px;
    color: var(--grey-text); font-size: 15px;
  }
  .office-details {
    position: absolute; left: 368px; top: 214px;
    color: #fff; font-size: 13px; line-height: 1.45;
    font-style: normal; white-space: nowrap;
  }
  .office-phone { font-weight: 700; font-size: 17px; margin-top: 8px; }

  .brand {
    position: absolute; left: 46px; top: 70px;
    display: flex; align-items: center; gap: 16px;
  }
  .brand-dot { width: 44px; height: 44px; border-radius: 50%; background: var(--blue); }
  .brand-name {
    color: var(--ink); font-weight: 700; font-size: 38px; line-height: 1.05;
  }
  .tagline {
    position: absolute; left: 46px; top: 222px;
    color: var(--orange); font-weight: 700; font-size: 21px;
  }
  .website {
    position: absolute; left: 46px; top: 256px;
    color: var(--grey-text); font-size: 15px; letter-spacing: 1.5px;
  }
</style>
</head>
<body>

<section class="card card-front">
  <div class="front-decoration" role="img" aria-label="Decorative orange, white and blue wave band"></div>
  <h1 class="holder-name">Darren Wolcott</h1>
  <p class="holder-degree">DDS, MSD</p>
  <p class="holder-email">info@brightbayortho.example</p>
  <address class="office-details">
    5214 West Linden Avenue, Suite 204<br>
    Cedarbrook, TX 76991
    <div class="office-phone">555-418-2637</div>
  </address>
</section>

<section class="card card-back">
  <div class="back-decoration" role="img" aria-label="Decorative orange, white and blue wave band"></div>
  <div class="brand">
    <span class="brand-dot"></span>
    <span class="brand-name">Brightbay<br>Orthodontics</span>
  </div>
  <p class="tagline">Braces for Adults &amp; Children</p>
  <p class="website">www.brightbayortho.example</p>
</section>

</body>
</html>
```